skyPARLOR Helicopter Tour WordPress Website Design

SkyPARLOR (skyparlor-example.com) is a premium helicopter tour company offering scenic flights in two Florida cities: Tampa and Sarasota. We are seeking a full Wordpress website redesign that is modern, upbeat, inviting, and highly conversion‑focused. The new site should feel energetic and trustworthy, reflect the excitement of helicopter sightseeing, and maintain our recognizable SkyPARLOR color palette—while updating the overall look to feel fresh, clean, and current.
The website must be SEO‑friendly, mobile‑optimized, and easy to navigate. It should highlight our 5‑star customer reviews, showcase our tours clearly, and integrate seamlessly with TrailDock for instant online booking. The design should support a premium aviation experience while remaining friendly and accessible to tourists, families, couples, and adventure seekers.

These elements are essential and must be included in the design:

Brand & UX:
- Modern, upbeat, inviting design
- SEO‑friendly structure and layout
- Easy navigation and clear user flow
- Light grey “SP” background logo watermark (as used on current site)
- Clean, aviation‑inspired typography and layout

Conversion Features:
- Instant booking above the fold (TrailDock integration)
- Live Orbin Ratings carousel
- Tour comparison table (duration, route, price, etc.)
- FAQ expandable section
- Gift Cards page (highlighted as a major offering)
- What to Expect timeline (Arrive → Check‑In → Safety Briefing → Flight → Photos)
- Weather transparency widget (clear messaging about weather‑dependent flights

Content Structure:
- Separate pages for Tampa, Sarasota, and Gender Reveal Flights
- Pilot/Team profiles with short bios
- Highlighted features:
- Doors‑Off option
- Sunset flights
- Romantic packages
- Champagne add‑ons

Colors:
Use the existing SkyPARLOR palette as the foundation, but modernize it.
- Background: Clean with the light grey “SP” watermark integrated tastefully.
The overall color direction should feel bright, premium, energetic, and trustworthy

Target Market(s)

Tourists visiting Tampa or Sarasota, Families looking for memorable activities, Couples seeking romantic experiences (sunset flights, proposals, anniversaries), Adventure seekers and content creators, Locals celebrating birthdays, holidays, or special occasions, Gender reveal clients looking for a unique aerial reveal experience

Industry/Entity Type

Travel & Tourism / Aviation / Helicopter Tours / Experience‑based Activities

Requirements
Must have
• These elements are essential and must be included in the design: Brand & UX - Modern, upbeat, inviting design / SEO‑friendly structure and layout / Easy navigation and clear user flow / Light grey “SP” background logo watermark (as used on current site) / Clean, aviation‑inspired typography and layout
Nice to have
• Interactive route map showing flight paths / Subtle motion or parallax effects in hero sections / Animated icons or micro‑interactions / Social media integration (Instagram grid, TikTok clips) / Sticky mobile booking bar / Video header or short aerial footage loop / Subtle aviation‑themed graphic elements (rotor blur, sky gradients, etc.
Should not have
• No dark, heavy, or overly moody themes / No outdated fonts or overly playful typography / No cluttered layouts or excessive text blocks / No stocky, generic tourism imagery / No slow‑loading animations or heavy effects that hurt SEO

```html
<!DOCTYPE html>
<html lang="en">
<head>
<meta charset="utf-8">
<title>SkyPARLOR — Helicopter Tours Over Tampa and Sarasota</title>
<link href="https://fonts.googleapis.com/css2?family=Saira+Extra+Condensed:wght@300;500;700&family=Plus+Jakarta+Sans:wght@400;500;600&display=swap" rel="stylesheet">
<style>
  :root{
    --hero-dark:#1b181d;
    --hero-mid:#3a2f35;
    --sunset:#b8743a;
    --page:#ececec;
    --ink:#161616;
    --muted:#4a4a4a;
    --white:#ffffff;
    --accent:#1f3f7a;
    --star:#f2b713;
    --line:rgba(255,255,255,.28);
    --watermark:rgba(0,0,0,.06);
  }
  *{box-sizing:border-box;margin:0;padding:0}
  html,body{width:1200px;height:800px;overflow:hidden;background:var(--page)}
  body{font-family:"Plus Jakarta Sans",sans-serif;color:var(--ink);position:relative}
  .display{font-family:"Saira Extra Condensed",sans-serif;text-transform:uppercase;letter-spacing:.01em}

  /* Hero */
  .hero{position:absolute;left:0;top:0;width:1200px;height:330px;overflow:hidden;color:var(--white)}
  .hero-photo{position:absolute;inset:0;
    background:
      linear-gradient(180deg,rgba(27,24,29,.55) 0%,rgba(27,24,29,0) 30%,rgba(27,24,29,.2) 60%,var(--hero-dark) 100%),
      linear-gradient(180deg,#4a4448 0%,#6d5a4e 28%,var(--sunset) 42%,#5a4350 55%,var(--hero-mid) 72%,var(--hero-dark) 100%);}
  .nav{position:absolute;left:0;top:0;width:100%;height:44px;display:flex;align-items:center;justify-content:space-between;padding:0 34px 0 66px;background:rgba(27,24,29,.35)}
  .brand{display:flex;align-items:center;gap:7px;font-weight:600;font-size:12px;letter-spacing:.06em}
  .brand-dot{width:14px;height:14px;border-radius:50%;background:var(--white)}
  .nav-links{display:flex;gap:10px;list-style:none;font-size:9px;align-items:center}
  .nav-links li+li::before{content:"•";margin-right:10px;opacity:.8}
  .search{display:flex;align-items:center;gap:6px;font-size:8.5px;padding:6px 12px;border-radius:20px;background:rgba(255,255,255,.1);border:1px solid rgba(255,255,255,.15)}
  .hero-copy{position:absolute;left:0;top:64px;width:100%;text-align:center}
  .hero-title{line-height:.92}
  .hero-title .light{display:block;font-weight:300;font-size:58px}
  .hero-title .line2{display:block;font-weight:300;font-size:64px}
  .hero-title strong{font-weight:700}
  .hero-sub{font-size:12px;margin-top:10px;opacity:.92}
  .badges{display:flex;justify-content:center;gap:8px;margin-top:18px}
  .badge{display:flex;flex-direction:column;justify-content:center;padding:0 14px;height:34px;border-radius:6px;background:rgba(20,18,22,.55);border:1px solid rgba(255,255,255,.18)}
  .badge-row{display:flex;align-items:center;gap:6px;font-family:"Saira Extra Condensed",sans-serif;font-weight:500;font-size:12px;letter-spacing:.02em}
  .badge small{font-size:6px;opacity:.7;margin-top:1px}
  .social-rail{position:absolute;right:72px;top:112px;display:flex;flex-direction:column;align-items:center;gap:9px}
  .social-rail .rule{width:1px;height:34px;background:var(--line)}
  .social-dot{width:8px;height:8px;border-radius:50%;border:1.5px solid var(--white)}

  /* Why section */
  .watermark{position:absolute;font-family:"Saira Extra Condensed",sans-serif;font-weight:700;color:var(--watermark);line-height:1}
  .why{position:absolute;left:66px;top:338px;width:1068px;height:86px;display:flex;justify-content:space-between;align-items:center}
  .why h2{font-size:36px;line-height:1;font-weight:300}
  .why h2 strong{font-weight:700}
  .why-aside{width:420px}
  .pill{display:inline-flex;align-items:center;gap:10px;padding:4px 4px 4px 14px;border-radius:30px;border:1px solid #cfcfcf;background:var(--white);font-size:12px;font-weight:500}
  .pill-arrow{width:22px;height:22px;border-radius:50%;background:var(--accent);display:flex;align-items:center;justify-content:center}
  .why-aside p{font-size:10.5px;line-height:1.4;margin-top:8px;color:var(--muted)}

  .video{position:absolute;left:66px;top:430px;width:1068px;height:140px;
    background:linear-gradient(180deg,#8b8a86 0%,#55606a 35%,#2c4250 65%,#1d3a3c 100%)}
  .play{position:absolute;left:50%;top:50%;width:36px;height:36px;margin:-18px 0 0 -18px;border-radius:50%;background:var(--white);display:flex;align-items:center;justify-content:center}

  /* Experiences */
  .experiences-head{position:absolute;left:0;top:582px;width:1200px;text-align:center}
  .experiences-head h2{font-size:36px;font-weight:300;line-height:1}
  .experiences-head h2 strong{font-weight:700}
  .experiences-head p{font-size:10.5px;margin-top:4px;color:var(--muted)}
  .tours{position:absolute;left:66px;top:650px;width:1068px;display:grid;grid-template-columns:repeat(4,1fr);gap:0 20px}
  .tour{display:flex;flex-direction:column;gap:6px}
  .tour-photo{height:96px;width:100%}
  .tour h3{font-size:11.5px;font-weight:700;line-height:1}
  .tour p{font-size:7px;line-height:1.35;color:var(--muted)}
  .tour a{font-size:7px;font-weight:600;color:var(--accent);text-decoration:underline;letter-spacing:.03em}
  .tour.offset{padding-top:0}
  .tour.offset .tour-photo{height:96px}
  .photo-skyline{background:linear-gradient(180deg,#a9c3df 0%,#7c8fa0 40%,#3d5a3a 70%,#1f3b4a 100%)}
  .photo-resort{background:linear-gradient(180deg,#2b2e3a 0%,#6a5a48 45%,#3c6f8e 80%,#2a5a78 100%)}
  .photo-bridge{background:linear-gradient(180deg,#9fc6e8 0%,#5fa6b3 35%,#23a3a1 65%,#1b7a83 100%)}
  .photo-reveal{background:linear-gradient(180deg,#8fb0d6 0%,#b7cde4 50%,#d9c6da 75%,#e9e4ea 100%)}
</style>
</head>
<body>

<header class="hero">
  <div class="hero-photo" role="img" aria-label="Aerial sunset view over a long bay bridge with purple lights reflecting on the water"></div>

  <nav class="nav">
    <div class="brand"><span class="brand-dot"></span><span>SKYPARLOR</span></div>
    <ul class="nav-links">
      <li>Home</li><li>Tours</li><li>Experiences</li><li>Gift Cards</li><li>What to Expect</li><li>About</li>
    </ul>
    <div class="search">
      <svg width="8" height="8" viewBox="0 0 10 10" fill="none" stroke="#fff" stroke-width="1.4"><circle cx="4.2" cy="4.2" r="3.2"/><line x1="6.6" y1="6.6" x2="9.2" y2="9.2"/></svg>
      <span>Search Now</span>
    </div>
  </nav>

  <div class="hero-copy">
    <h1 class="hero-title display">
      <span class="light">See Florida</span>
      <span class="line2">Like <strong>Never Before</strong></span>
    </h1>
    <p class="hero-sub">Premium Helicopter Tours Over Tampa And Sarasota.</p>
    <div class="badges">
      <div class="badge">
        <div class="badge-row">
          <svg width="10" height="10" viewBox="0 0 10 10"><polygon points="5,0.5 6.3,3.6 9.6,3.8 7.1,6 7.9,9.3 5,7.5 2.1,9.3 2.9,6 0.4,3.8 3.7,3.6" fill="var(--star)"/></svg>
          <span>5.0 Rated on Orbin</span>
        </div>
      </div>
      <div class="badge">
        <div class="badge-row"><span>FAA Certified Pilots</span></div>
        <small>Thousands of Happy Flyers</small>
      </div>
    </div>
  </div>

  <div class="social-rail" aria-label="Social links">
    <span class="rule"></span>
    <span class="social-dot"></span>
    <span class="social-dot"></span>
    <span class="social-dot"></span>
    <span class="rule"></span>
  </div>
</header>

<main>
  <span class="watermark" style="left:58px;top:326px;font-size:70px" aria-hidden="true">SP</span>

  <section class="why">
    <h2 class="display">Why SkyPARLOR Is<br><strong>Florida’s Most Trusted</strong></h2>
    <div class="why-aside">
      <span class="pill">Book Your Tour
        <span class="pill-arrow"><svg width="9" height="9" viewBox="0 0 10 10" fill="none" stroke="#fff" stroke-width="1.5"><line x1="2" y1="8" x2="8" y2="2"/><polyline points="3.5,2 8,2 8,6.5"/></svg></span>
      </span>
      <p>We Deliver A Premium, Safe, And Memorable<br>Aviation Experience From Takeoff To Landing.</p>
    </div>
  </section>

  <div class="video" role="img" aria-label="Aerial dusk footage of a waterfront marina and city skyline">
    <span class="play"><svg width="10" height="10" viewBox="0 0 10 10"><polygon points="3,2 8,5 3,8" fill="var(--accent)"/></svg></span>
  </div>

  <span class="watermark" style="left:300px;top:576px;font-size:60px" aria-hidden="true">SP</span>

  <section class="experiences-head">
    <h2 class="display">Our Signature <strong>Helicopter Experiences</strong></h2>
    <p>Fly Above Downtown Tampa, Bays, And Iconic Landmarks.</p>
  </section>

  <section class="tours">
    <article class="tour">
      <div class="tour-photo photo-skyline" role="img" aria-label="Tampa city skyline above a tree-lined river"></div>
      <h3 class="display">Tampa Skyline Discovery Tour</h3>
      <p>A perfect introduction to Tampa’s iconic skyline and waterfront views.</p>
      <a>VIEW DETAILS ↗</a>
    </article>
    <article class="tour offset">
      <h3 class="display">Sarasota Coastal Escape Tour</h3>
      <p>Soar above crystal-clear coastlines and breathtaking beaches.</p>
      <a>VIEW DETAILS ↗</a>
      <div class="tour-photo photo-resort" role="img" aria-label="Waterfront resort building with a lit pool at dusk"></div>
    </article>
    <article class="tour">
      <div class="tour-photo photo-bridge" role="img" aria-label="Causeway bridge crossing turquoise coastal water"></div>
      <h3 class="display">Ultimate Florida Aerial Adventure</h3>
      <p>The most immersive helicopter experience SkyPARLOR has to offer.</p>
      <a>VIEW DETAILS ↗</a>
    </article>
    <article class="tour offset">
      <h3 class="display">Gender Reveal Celebration Flight</h3>
      <p>Turn your special moment into an unforgettable aerial celebration.</p>
      <a>VIEW DETAILS ↗</a>
      <div class="tour-photo photo-reveal" role="img" aria-label="Small aircraft releasing pink and blue smoke in a cloudy sky"></div>
    </article>
  </section>
</main>

</body>
</html>
```